BRIGHT RIVER POWER.

I'd like my business logo.
contact name: Dennis Halvorsen
phone:0438759164
email: info@brightriverpower.net.au
website: www.brightriverpower.net.au

services:
solar
battery storage
LED lighting
energy saving solutions
general electrical
I'd like the design to look professional

Target Market(s)

Everyone

Industry/Entity Type

Business

Contact Information for Business Card

as described above

Requirements
Must have
• Id like the colours and the design to work well with my logo.

```html
<!DOCTYPE html>
<html lang="en">
<head>
<meta charset="utf-8">
<title>Bright River Power – Business Card</title>
<link href="https://fonts.googleapis.com/css2?family=Open+Sans:wght@400;600;700&display=swap" rel="stylesheet">
<style>
  :root {
    --page-bg: #e9ebe6;
    --green-deep: #3f9a2a;
    --green-mid: #5cb531;
    --green-light: #9fd15a;
    --green-text: #4aa12e;
    --ink: #3a3a3a;
    --white: #ffffff;
    --name-tint: #e3efd9;
  }
  * { margin: 0; padding: 0; box-sizing: border-box; }
  html, body { width: 1200px; height: 843px; overflow: hidden; }
  body {
    background: var(--page-bg);
    font-family: "Open Sans", Arial, sans-serif;
    position: relative;
  }
  .card {
    position: absolute;
    width: 520px;
    height: 297px;
    border-radius: 18px;
    overflow: hidden;
    box-shadow: 0 10px 28px rgba(0,0,0,0.18);
  }

  /* Back side */
  .card--back {
    left: 80px; top: 110px;
    background: radial-gradient(circle at 40% 40%, var(--green-light) 0%, var(--green-mid) 45%, var(--green-deep) 100%);
    color: var(--white);
  }
  .services {
    position: absolute;
    right: 34px; top: 28px;
    list-style: none;
    text-align: right;
    font-size: 15px;
    line-height: 21px;
  }
  .services li::after {
    content: "";
    display: inline-block;
    width: 7px; height: 7px;
    border-radius: 50%;
    background: var(--white);
    margin-left: 10px;
    vertical-align: middle;
  }
  .back-brand {
    position: absolute;
    right: 34px; top: 160px;
    font-size: 30px;
    font-weight: 700;
    letter-spacing: 1px;
    color: var(--white);
  }

  /* Front side */
  .card--front {
    left: 600px; top: 436px;
    background: var(--white);
  }
  .front-art {
    position: absolute;
    left: 255px; top: 45px;
    right: 0; bottom: 0;
    border-top-left-radius: 100% 100%;
    background: linear-gradient(45deg, var(--green-light) 0%, var(--green-mid) 50%, var(--green-deep) 100%);
  }
  .front-brand {
    position: absolute;
    left: 30px; top: 32px;
    display: flex; align-items: center; gap: 10px;
    font-size: 22px;
    font-weight: 700;
    color: var(--green-text);
  }
  .front-brand .mark {
    width: 22px; height: 22px; border-radius: 50%;
    background: var(--green-text);
  }
  .contacts {
    position: absolute;
    left: 30px; top: 140px;
    list-style: none;
    font-size: 14px;
    color: var(--ink);
    line-height: 22px;
  }
  .contacts li { display: flex; align-items: center; gap: 8px; }
  .contacts svg { width: 13px; height: 13px; fill: var(--green-text); flex: none; }
  .contact-name {
    position: absolute;
    right: 40px; bottom: 36px;
    font-size: 19px;
    font-weight: 600;
    color: var(--name-tint);
  }
</style>
</head>
<body>

<section class="card card--back">
  <ul class="services">
    <li>Solar</li>
    <li>Battery storage</li>
    <li>LED lighting</li>
    <li>Energy saving solutions</li>
    <li>General electrical</li>
  </ul>
  <div class="back-brand">BRIGHT RIVER POWER</div>
</section>

<section class="card card--front">
  <div class="front-art" role="img" aria-label="Green leaf swoosh illustration"></div>

  <div class="front-brand"><span class="mark"></span>BRIGHT RIVER POWER</div>

  <ul class="contacts">
    <li><svg viewBox="0 0 24 24"><path d="M6.6 10.8a15 15 0 0 0 6.6 6.6l2.2-2.2a1 1 0 0 1 1-.25 11.4 11.4 0 0 0 3.6.57 1 1 0 0 1 1 1V20a1 1 0 0 1-1 1A17 17 0 0 1 3 4a1 1 0 0 1 1-1h3.5a1 1 0 0 1 1 1c0 1.25.2 2.45.57 3.57a1 1 0 0 1-.25 1z"/></svg>0438759164</li>
    <li><svg viewBox="0 0 24 24"><path d="M2 5h20v14H2z M2 5l10 8 10-8" stroke="#fff" stroke-width="1.5"/></svg>info@brightriverpower.net.au</li>
    <li><svg viewBox="0 0 24 24"><circle cx="12" cy="12" r="10"/><path d="M2 12h20M12 2c3 3 3 17 0 20M12 2c-3 3-3 17 0 20" stroke="#fff" stroke-width="1.5" fill="none"/></svg>www.brightriverpower.net.au</li>
  </ul>

  <div class="contact-name">Dennis Halvorsen</div>
</section>

</body>
</html>
```